Dorrance's Anvil BBQ Sauce Needs a Label

We are looking for a rustic label that would help our product stand out on a shelf. The company name is Dorrance's Anvil. We are a new company looking to stand out on shelving with our amazing BBQ Sweet, Spicy and Rub. The label size needs to be 6.5" wide x 2.5" tall. I have taken a step in creating a label which is attached. This is just an idea for you to bring us an amazing retail ready look. On the left side of the label we need to have a 1 color flag with Made In USA. Also would need to have the address on the same side. Dorrance's Anvil BBQ Sauce, Palm Hollow, FL 33999. The nutrition Facts are also needed. The information is correct but would need to be adjusted as to font and sizing. Image 7247 is what I have lightly put together and image 2495 is current logo on actual label. If you need any more guidance please let me know. Merles TangFire is an example of the pop we would like to see

Requirements
Must have
• Rustic Look
Nice to have
• Rustic look with a feeling similar to image 7247 that’s attached.
Should not have
• Same look as the original logo that’s on the actual label.

```html
<!DOCTYPE html>
<html lang="en">
<head>
<meta charset="utf-8">
<title>Dorrance's Anvil BBQ Sauce – Labels</title>
<link href="https://fonts.googleapis.com/css2?family=Nunito+Sans:wght@400;600;800;900&display=swap" rel="stylesheet">
<style>
  :root{
    --page:#ffffff;
    --paper-light:#f3e8cb;
    --paper-dark:#e4cfa0;
    --ink:#3a2624;
    --spicy:#c8213a;
    --sweet:#2f47a0;
    --rub:#e2621d;
  }
  *{box-sizing:border-box;margin:0;padding:0}
  html,body{width:1050px;height:1200px;overflow:hidden;background:var(--page)}
  body{font-family:"Nunito Sans",Arial,sans-serif;color:var(--ink);position:relative}
  .label{
    position:absolute;left:60px;width:930px;height:357px;
    background:radial-gradient(ellipse at 20% 20%,var(--paper-dark),transparent 55%),
               linear-gradient(135deg,var(--paper-light),var(--paper-dark));
    overflow:hidden;
  }
  .label--spicy{top:40px;--accent:var(--spicy)}
  .label--sweet{top:421px;--accent:var(--sweet)}
  .label--rub{top:803px;--accent:var(--rub)}
  .label__band{position:absolute;left:0;right:0;bottom:0;height:15px;border-top:9px solid var(--accent);background:var(--ink)}
  .info{position:absolute;left:21px;top:24px;width:200px;font-size:10.5px;line-height:13px}
  .info__title{font-weight:800}
  .info__note{font-weight:800;margin-top:13px}
  .origin{position:absolute;left:21px;top:217px;font-size:10.5px;line-height:13px}
  .flag{display:block;width:86px;height:43px;background:var(--ink)}
  .origin__mark{font-weight:900;font-size:12px;margin-top:4px;letter-spacing:.3px}
  .origin__address{font-weight:800;margin-top:10px}
  .origin__web{font-weight:800;margin-top:8px}
  .brand{position:absolute;left:285px;top:40px;width:358px;text-align:center}
  .brand__name{font-weight:900;font-size:44px;line-height:46px;text-transform:uppercase;color:var(--ink)}
  .flavor{position:absolute;left:410px;top:286px;width:108px;height:28px;border:2px solid var(--ink);background:var(--paper-light);
    font-weight:900;font-size:16px;letter-spacing:1px;text-align:center;line-height:24px;color:var(--accent)}
  .size{position:absolute;left:573px;top:290px;font-weight:900;font-size:19px}
  .facts{position:absolute;left:744px;top:19px;width:163px;height:316px;border:1.5px solid var(--ink);padding:5px 7px;font-size:8.6px;line-height:11px}
  .label--rub .facts{height:224px}
  .facts__title{font-weight:900;font-size:17px;line-height:18px;letter-spacing:.4px}
  .facts__row{display:flex;justify-content:space-between;border-bottom:.8px solid var(--ink);padding:2.6px 0}
  .facts__row--plain{border-bottom:none;padding:0}
  .facts__row--sub{padding-left:9px}
  .facts__bar{height:7px;background:var(--ink);margin:3px 0}
  .facts b{font-weight:800}
  .facts__small{font-size:6px;line-height:7px;padding-top:2px;text-align:justify}
  .facts__right{text-align:right;font-weight:800;font-size:7px}
</style>
</head>
<body>

<article class="label label--spicy">
  <section class="info"><p class="info__title">Ingredients:</p><p>Tomato, Chili Sauce,<br>Vinegar, Worcester,<br>Sugar, Onion, Lemon,<br>Honey and Spices</p><p class="info__note">Refrigerate After Opening</p></section>
  <section class="origin"><span class="flag" role="img" aria-label="One-colour American flag"></span><p class="origin__mark">MADE IN USA</p><p class="origin__address">Dorrance's Anvil BBQ Sauce<br>Palm Hollow, FL 33999</p><p class="origin__web">www.dorrancesanvilbbq.com</p></section>
  <div class="brand"><p class="brand__name">Dorrance's<br>Anvil<br>BBQ Sauce</p></div>
  <p class="flavor">SPICY</p><p class="size">16 oz.</p>
  <section class="facts">
    <p class="facts__title">Nutrition Facts</p>
    <p class="facts__row facts__row--plain"><span>Serving Size 1 Tbsp. (18g)</span></p>
    <p class="facts__row facts__row--plain"><span>Servings Per Container</span><span>25</span></p>
    <div class="facts__bar"></div>
    <p class="facts__row" style="font-size:7.5px"><b>Amount Per Serving</b></p>
    <p class="facts__row"><span><b>Calories</b> 25</span><span>Calories from Fat 0</span></p>
    <p class="facts__right">% Daily Value*</p>
    <p class="facts__row"><span><b>Total Fat</b> 0g</span><b>0%</b></p>
    <p class="facts__row facts__row--sub"><span>Saturated Fat 0g</span><b>0%</b></p>
    <p class="facts__row facts__row--sub"><span>Trans Fat 0g</span></p>
    <p class="facts__row"><span><b>Cholesterol</b> 0mg</span><b>0%</b></p>
    <p class="facts__row"><span><b>Sodium</b> 150mg</span><b>6%</b></p>
    <p class="facts__row"><span><b>Total Carbohydrate</b> 6g</span><b>2%</b></p>
    <p class="facts__row facts__row--sub"><span>Dietary Fiber 0g</span><b>0%</b></p>
    <p class="facts__row facts__row--sub"><span>Sugars 6g</span></p>
    <p class="facts__row facts__row--plain"><span><b>Protein</b> 0.2g</span></p>
    <div class="facts__bar"></div>
    <p class="facts__row"><span>Vitamin A 1%</span><span>• Vitamin C 1%</span></p>
    <p class="facts__row"><span>Calcium 1%</span><span>• Iron 1%</span></p>
    <p class="facts__small">*Percent Daily Values are based on a 2,000 calorie diet. Your daily values may be higher or lower depending on your calorie needs</p>
  </section>
  <div class="label__band"></div>
</article>

<article class="label label--sweet">
  <section class="info"><p class="info__title">Ingredients:</p><p>Tomato, Chili Sauce,<br>Vinegar, Worcester,<br>Sugar, Onion, Lemon,<br>Honey and Spices</p><p class="info__note">Refrigerate After Opening</p></section>
  <section class="origin"><span class="flag" role="img" aria-label="One-colour American flag"></span><p class="origin__mark">MADE IN USA</p><p class="origin__address">Dorrance's Anvil BBQ Sauce<br>Palm Hollow, FL 33999</p><p class="origin__web">www.dorrancesanvilbbq.com</p></section>
  <div class="brand"><p class="brand__name">Dorrance's<br>Anvil<br>BBQ Sauce</p></div>
  <p class="flavor">SWEET</p><p class="size">16 oz.</p>
  <section class="facts">
    <p class="facts__title">Nutrition Facts</p>
    <p class="facts__row facts__row--plain"><span>Serving Size 1 Tbsp. (18g)</span></p>
    <p class="facts__row facts__row--plain"><span>Servings Per Container</span><span>25</span></p>
    <div class="facts__bar"></div>
    <p class="facts__row" style="font-size:7.5px"><b>Amount Per Serving</b></p>
    <p class="facts__row"><span><b>Calories</b> 25</span><span>Calories from Fat 0</span></p>
    <p class="facts__right">% Daily Value*</p>
    <p class="facts__row"><span><b>Total Fat</b> 0g</span><b>0%</b></p>
    <p class="facts__row facts__row--sub"><span>Saturated Fat 0g</span><b>0%</b></p>
    <p class="facts__row facts__row--sub"><span>Trans Fat 0g</span></p>
    <p class="facts__row"><span><b>Cholesterol</b> 0mg</span><b>0%</b></p>
    <p class="facts__row"><span><b>Sodium</b> 150mg</span><b>6%</b></p>
    <p class="facts__row"><span><b>Total Carbohydrate</b> 6g</span><b>2%</b></p>
    <p class="facts__row facts__row--sub"><span>Dietary Fiber 0g</span><b>0%</b></p>
    <p class="facts__row facts__row--sub"><span>Sugars 6g</span></p>
    <p class="facts__row facts__row--plain"><span><b>Protein</b> 0.2g</span></p>
    <div class="facts__bar"></div>
    <p class="facts__row"><span>Vitamin A 1%</span><span>• Vitamin C 1%</span></p>
    <p class="facts__row"><span>Calcium 1%</span><span>• Iron 1%</span></p>
    <p class="facts__small">*Percent Daily Values are based on a 2,000 calorie diet. Your daily values may be higher or lower depending on your calorie needs</p>
  </section>
  <div class="label__band"></div>
</article>

<article class="label label--rub">
  <section class="info"><p class="info__title">Assorted Spices:</p><p>Tomato, Chili Sauce,<br>Vinegar, Worcester,<br>Sugar, Onion, Lemon,<br>Honey and Spices</p></section>
  <section class="origin"><span class="flag" role="img" aria-label="One-colour American flag"></span><p class="origin__mark">MADE IN USA</p><p class="origin__address">Dorrance's Anvil BBQ Sauce<br>Palm Hollow, FL 33999</p><p class="origin__web">www.dorrancesanvilbbq.com</p></section>
  <div class="brand"><p class="brand__name">Dorrance's<br>Anvil<br>BBQ Sauce</p></div>
  <p class="flavor">RUB</p><p class="size">8 Oz.</p>
  <section class="facts">
    <p class="facts__title">Nutrition Facts</p>
    <p class="facts__row facts__row--plain"><span>Serving Size 1 Tsp. (5g)</span></p>
    <p class="facts__row facts__row--plain"><span>Servings Per Container</span><span>45</span></p>
    <div class="facts__bar"></div>
    <p class="facts__row" style="font-size:7.5px"><b>Amount Per Serving</b></p>
    <p class="facts__row"><span><b>Calories</b> 0</span></p>
    <p class="facts__right">% Daily Value*</p>
    <p class="facts__row"><span><b>Total Fat</b> 0g</span><b>0%</b></p>
    <p class="facts__row"><span><b>Sodium</b> 70mg</span><b>3%</b></p>
    <p class="facts__row"><span><b>Total Carbohydrate</b> 0mg</span><b>0%</b></p>
    <p class="facts__row facts__row--plain"><span><b>Protein</b> 0g</span></p>
    <div class="facts__bar"></div>
    <p class="facts__small">Not a significant source of calories from fat, saturated fat, trans fat, cholesterol, dietary fiber, sugars, vitamin A, vitamin C, calcium, iron.</p>
    <p class="facts__small">*Percent Daily Values are based on a 2,000 calorie diet.</p>
  </section>
  <div class="label__band"></div>
</article>

</body>
</html>
```